I'm looking for a rack card or trifold brochure to advertise elective ultrasounds

I need something that looks professional but eye catching to bring to doctor's office for display. I want it to have my logo, some 3D images and have a cohesive design. I want it to give a summary of what I offer in terms of elective ultrasounds: Peace of mind, early gender, 3D/4D. It should also mention that I can travel to the patient for in-home ultrasounds. (size around 4 x 9" rack card or trifold brochure)

Target Market(s)

Expecting moms and families

Industry/Entity Type

Elective 3D 4D private ultrasounds

Colors
E54698
E96AAD
F1A4CE
F9D9EA
FCEFF6

Requirements
Must have
• A focus on the elective portion of my business--offering the most amazing 3D images around (maybe not those words exactly). Offering on site and in-home services. Packages include Peace of Mind, Early gender, and 3D/4D imaging. Professional and experienced sonographer with 15+ years experience. Include 3d images. For this brochure, I don't want to mention the diagnostics portion as I will be bringing them to OBGYN office to hopefully display. I would like a "What we offer" section including -Conveniently located in Troy, NY or book in your home! -Early peace of mind ultrasounds starting at 6 weeks -Early gender determination starting at 13 weeks -A large, comfortable viewing space to bring your family. Kids are always welcome! -Top of the line technology to guarantee you will get the best possible images of your baby -Discounts for repeat families in the same pregnancy -Heartbeat animals to record baby's heartbeat -Gender reveal extinguishers, cannons, and balloons -3D face to Realistic AI transformation I would prefer for my face not to be on the brochure.
Nice to have
• A QR code linking the website
Should not have
• A sloppy presentation, I do not want to mention the diagnostic side of the business in these advertisements

```html
<!DOCTYPE html>
<html lang="en">
<head>
<meta charset="utf-8">
<title>Cradle View Ultrasound – Rack Card</title>
<link rel="stylesheet" href="https://fonts.googleapis.com/css2?family=Barlow:wght@400;500;700&display=swap">
<style>
  :root {
    --backdrop: #a7a7a7;
    --card-white: #ffffff;
    --pink-strong: #e54698;
    --pink-mid: #e96aad;
    --pink-soft: #f1a4ce;
    --pink-pale: #f9d9ea;
    --pink-mist: #fcf3f8;
    --ink: #22252b;
    --brand-ink: #3d4d5a;
    --skin-light: #e8a27c;
    --skin-deep: #9c4a2c;
  }
  * { box-sizing: border-box; margin: 0; padding: 0; }
  html, body {
    width: 1200px; height: 1200px; overflow: hidden;
    background: var(--backdrop);
    font-family: "Barlow", Arial, sans-serif;
  }
  .rack-card {
    position: absolute; left: 364px; top: 69px;
    width: 472px; height: 1060px;
    background: var(--card-white);
    overflow: hidden;
  }
  .rack-card__wave { position: absolute; inset: 0; }
  .brand {
    position: absolute; left: 0; width: 310px; top: 238px;
    text-align: center; color: var(--brand-ink);
    font-weight: 500;
  }
  .brand__name { font-size: 34px; line-height: 1; }
  .brand__tag { font-size: 14px; letter-spacing: 4px; margin-top: 8px; }
  .headline {
    position: absolute; right: 38px; top: 392px;
    text-align: right; color: var(--card-white);
    font-weight: 500; text-shadow: 3px 3px 5px rgba(80, 20, 50, .55);
  }
  .headline__lead { font-size: 62px; line-height: 1; letter-spacing: 1px; }
  .headline__sub { font-size: 40px; line-height: 1.22; font-weight: 700; }
  .scan {
    position: absolute; border-radius: 50%;
    background: radial-gradient(circle at 45% 40%, var(--skin-light), var(--skin-deep) 85%);
  }
  .scan--left { left: 70px; top: 578px; width: 182px; height: 182px; }
  .scan--right {
    left: 237px; top: 597px; width: 224px; height: 224px;
    border: 3px solid var(--card-white);
    background: radial-gradient(circle at 50% 42%, #f0a880, #b0552f 70%, #3a1a10 100%);
  }
  .packages {
    position: absolute; left: 49px; top: 768px;
    list-style: none; color: var(--ink);
    font-size: 21px; line-height: 27.5px;
  }
  .packages li::before { content: "» "; }
  .about {
    position: absolute; left: 49px; top: 904px; width: 400px;
    color: var(--ink); font-size: 17px; line-height: 25px;
  }
  .about p + p { margin-top: 22px; }
</style>
</head>
<body>
  <article class="rack-card">
    <svg class="rack-card__wave" width="472" height="1060" viewBox="0 0 472 1060" aria-hidden="true">
      <defs>
        <linearGradient id="panelPink" x1="1" y1="0" x2="0.3" y2="1">
          <stop offset="0" stop-color="#e54698"/>
          <stop offset="0.35" stop-color="#e96aad"/>
          <stop offset="0.7" stop-color="#f1a4ce"/>
          <stop offset="1" stop-color="#fcf3f8"/>
        </linearGradient>
      </defs>
      <path d="M0 432 C 130 390, 250 370, 340 300 C 400 252, 430 214, 472 198 L472 1060 L0 1060 Z" fill="url(#panelPink)"/>
    </svg>

    <div class="brand">
      <div class="brand__name">Cradle View</div>
      <div class="brand__tag">ULTRASOUND</div>
    </div>

    <h1 class="headline">
      <span class="headline__lead">ON SITE</span><br>
      <span class="headline__sub">AND IN-HOME<br>SERVICES</span>
    </h1>

    <div class="scan scan--left" role="img" aria-label="3D ultrasound image of a baby"></div>
    <div class="scan scan--right" role="img" aria-label="3D ultrasound image of a baby"></div>

    <ul class="packages">
      <li>Packages include</li>
      <li>Peace of Mind</li>
      <li>Early gender</li>
      <li>3D/4D imaging</li>
    </ul>

    <div class="about">
      <p>Professional and experienced sonographer<br>with 15+ years experience.</p>
      <p>Include 3d images.</p>
    </div>
  </article>
</body>
</html>
```